Boutique Health and Fitness Personal Training Studio

I would like to have a brochure designed which provides a detailed description of the services offered in my business.
I have personal training studio, We look after people from early 20's to 90's, healthy to very unhealthy.
We conduct:
A consultation
An assessment
A personalised program
Personalised training sessions
I would like to base the design around the colours of my logo (attached) and use some of (or all of) the images and information I have also attached.
I would be happy with your own images included also.

Target Market(s)

20 to 90 year olds

Industry/Entity Type

Business

Font styles to use
Serif
Sans Serif

Colors
9bcb3c
add136
cadf82
eaf2ce

Requirements
Must have
• Colour and images of fitness.
• 8.5x14 legal
• Tri fold
• 2 folds with 3 faces back n front
Nice to have
• The feeling of wellbeing
Should not have
• This is not a gym.
• It should have the feel of a private relaxed environment

```html
<!DOCTYPE html>
<html lang="en">
<head>
<meta charset="utf-8">
<title>Green Path Studio – Tri-fold Brochure</title>
<link rel="stylesheet" href="https://fonts.googleapis.com/css2?family=Lato:wght@400;700&family=Roboto+Condensed:wght@300;400;700&display=swap">
<style>
  :root {
    --page-bg: #ece9e4;
    --green: #5f8f2a;
    --green-dark: #466d1c;
    --green-bright: #7db135;
    --ink: #111111;
    --white: #ffffff;
    --charcoal: #2b2d2a;
    --mist: #e4e4e4;
  }
  * { margin: 0; padding: 0; box-sizing: border-box; }
  html, body { width: 1200px; height: 907px; overflow: hidden; background: var(--page-bg); }
  .brochure {
    position: absolute; left: 40px; top: 113px;
    width: 1120px; height: 680px; overflow: hidden;
    font-family: "Lato", Arial, sans-serif;
  }
  .brochure-art { position: absolute; inset: 0; }
  .txt { position: absolute; }

  /* Left panel */
  .section-head {
    font-family: "Roboto Condensed", Arial, sans-serif; font-weight: 700;
    font-size: 19px; color: var(--ink); display: flex; align-items: center; gap: 8px;
  }
  .section-head .bullet { width: 18px; height: 18px; border-radius: 50%; background: var(--white); }
  .sessions-copy {
    left: 46px; top: 86px; width: 302px; color: var(--white);
    font-size: 11.6px; line-height: 1.38; text-align: justify;
  }
  .plain-line { color: var(--white); font-family: "Roboto Condensed", Arial, sans-serif; font-size: 17px; }
  .parking { font-family: "Roboto Condensed", Arial, sans-serif; font-weight: 700; font-size: 20px; color: var(--ink); }

  /* Middle panel */
  .contact { left: 373px; width: 374px; text-align: center; }
  .brand {
    display: flex; align-items: center; justify-content: center; gap: 9px;
    font-family: "Lato", Arial, sans-serif; font-weight: 700; font-size: 22px;
  }
  .brand .dot { width: 20px; height: 20px; border-radius: 50%; }
  .brand-green { color: var(--green); }
  .brand-green .dot { background: var(--green); }
  .brand-white { color: var(--white); }
  .brand-white .dot { background: var(--white); }
  .contact-key { font-family: "Roboto Condensed", Arial, sans-serif; font-weight: 700; font-size: 18px; color: var(--green-dark); line-height: 1.25; }
  .contact-line { font-size: 12.5px; color: var(--ink); font-weight: 700; }
  .contact-line.addr { font-weight: 400; }

  /* Right panel */
  .experience { right: 40px; top: 458px; text-align: right; font-family: "Roboto Condensed", Arial, sans-serif; }
  .experience .lead { color: var(--green-bright); font-weight: 700; font-size: 25px; line-height: 1.2; }
  .experience .line { color: var(--white); font-weight: 300; font-size: 24px; line-height: 1.3; }
</style>
</head>
<body>
<div class="brochure">
  <svg class="brochure-art" width="1120" height="680" viewBox="0 0 1120 680" xmlns="http://www.w3.org/2000/svg">
    <defs>
      <linearGradient id="leftGreen" x1="0" y1="0" x2="1" y2="1">
        <stop offset="0" stop-color="#6c9c30"/>
        <stop offset="1" stop-color="#4f7c22"/>
      </linearGradient>
      <linearGradient id="midMist" x1="0" y1="0" x2="1" y2="0">
        <stop offset="0" stop-color="#e9e9e9"/>
        <stop offset="0.5" stop-color="#ffffff"/>
        <stop offset="1" stop-color="#e2e2e2"/>
      </linearGradient>
      <linearGradient id="runnerTone" x1="0" y1="0" x2="0" y2="1">
        <stop offset="0" stop-color="#e8e8e8" stop-opacity="0"/>
        <stop offset="1" stop-color="#cfcfcf"/>
      </linearGradient>
      <linearGradient id="foodTone" x1="0" y1="0" x2="1" y2="0">
        <stop offset="0" stop-color="#6f9a3c"/>
        <stop offset="0.45" stop-color="#c9a24a"/>
        <stop offset="0.75" stop-color="#8d8d8d"/>
        <stop offset="1" stop-color="#6b5a45"/>
      </linearGradient>
      <linearGradient id="massageTone" x1="0" y1="0" x2="1" y2="0">
        <stop offset="0" stop-color="#b83a3a"/>
        <stop offset="0.6" stop-color="#d8d8d8"/>
        <stop offset="1" stop-color="#f2f2f2"/>
      </linearGradient>
      <linearGradient id="trainerTone" x1="0" y1="0" x2="1" y2="1">
        <stop offset="0" stop-color="#4a5560"/>
        <stop offset="0.55" stop-color="#9c7a64"/>
        <stop offset="1" stop-color="#2c3238"/>
      </linearGradient>
    </defs>

    <!-- left panel -->
    <rect class="panel-left" x="0" y="0" width="373" height="680" fill="url(#leftGreen)"/>
    <path role="img" aria-label="Photo: trainer guiding a client's back during a gym exercise" d="M0,385 Q250,375 345,680 L0,680 Z" fill="url(#massageTone)"/>
    <path class="curve-white" d="M0,378 Q258,368 354,680" fill="none" stroke="var(--white)" stroke-width="7"/>
    <path class="curve-green" d="M0,366 Q270,355 372,680" fill="none" stroke="var(--green-dark)" stroke-width="6"/>

    <!-- middle panel -->
    <rect class="panel-middle" x="373" y="0" width="374" height="680" fill="url(#midMist)"/>
    <rect role="img" aria-label="Faded photo: woman running outdoors" x="470" y="340" width="180" height="180" fill="url(#runnerTone)" opacity="0.7"/>
    <path role="img" aria-label="Photo: fresh vegetables, dumbbells, tape measure and water bottle" d="M373,680 L373,505 L420,505 Q440,475 470,490 Q500,462 540,478 L560,470 L600,482 L640,470 L690,480 L747,470 L747,680 Z" fill="url(#foodTone)"/>

    <!-- right panel -->
    <rect class="panel-right" x="747" y="0" width="373" height="680" fill="#eeeeee"/>
    <path role="img" aria-label="Photo: muscular man training on a cable machine" d="M805,0 L1120,0 L1120,312 Q1010,348 930,338 C830,320 770,180 805,0 Z" fill="url(#trainerTone)"/>
    <path class="frame-green" d="M805,0 C770,180 830,320 930,338 Q1010,348 1120,312" fill="none" stroke="var(--green)" stroke-width="9"/>
    <path class="dark-base" d="M747,680 L747,590 Q880,395 1120,360 L1120,680 Z" fill="var(--charcoal)"/>
    <path class="arc-green" d="M747,582 Q878,385 1120,350" fill="none" stroke="var(--green)" stroke-width="9"/>
    <path class="arc-green-thin" d="M760,590 Q890,400 1120,370" fill="none" stroke="var(--green-bright)" stroke-width="2"/>
  </svg>

  <!-- left panel text -->
  <div class="txt section-head" style="left:46px; top:58px;"><span class="bullet"></span>Your sessions</div>
  <p class="txt sessions-copy">Training at the studio is professional and caring, but focused and challenging. Typically each session will take approximately 60 minutes. Training times can be organized to suit your needs with early mornings and evenings available.</p>
  <div class="txt section-head" style="left:46px; top:190px;"><span class="bullet"></span>The Cost</div>
  <div class="txt plain-line" style="left:52px; top:224px;">$45 paid in blocks of 5 or 10 sessions</div>
  <div class="txt section-head" style="left:46px; top:258px;"><span class="bullet"></span>Health fund claimable</div>
  <div class="txt plain-line" style="left:54px; top:291px;">Open 7 days</div>
  <div class="txt parking" style="left:52px; top:322px;">Ample private parking available</div>

  <!-- middle panel text -->
  <div class="txt contact" style="top:132px;">
    <div class="brand brand-green"><span class="dot"></span>Green Path Studio</div>
  </div>
  <div class="txt contact" style="top:186px;">
    <div class="contact-key">Unit 12</div>
    <div class="contact-key">Level 2</div>
    <div class="contact-line addr" style="margin-top:5px;">48 Wattle Grove Lane Ridgeview</div>
    <div class="contact-line" style="margin-top:4px;"><span class="contact-key">call-</span>0400 555 217</div>
    <div class="contact-key" style="margin-top:3px;">visit us</div>
    <div class="contact-line">www.greenpathstudio.com.au</div>
  </div>

  <!-- right panel text -->
  <div class="txt experience">
    <div class="lead">OVER 25 YEARS OF</div>
    <div class="line">experience managing</div>
    <div class="line">the health and fitness</div>
  </div>
  <div class="txt" style="left:775px; top:604px; width:320px;">
    <div class="brand brand-white"><span class="dot"></span>Green Path Studio</div>
  </div>
</div>
</body>
</html>
```